Local fast-growing company in the service sector

We are looking for a modern business card design, which should also appear on our letterheads

Target Market(s)

Private and industrial sectors

Contact Information for Business Card

Vorname Name
Kellberger Str. 18
71489 Kellbach
Tel.: 07146-839214-0
Name@agentur-kvtl.de

Colors
9d9d9d
919191
aaaaaa

Requirements
Must have
• The logo (file) in silver

```html
<!DOCTYPE html>
<html lang="de">
<head>
<meta charset="utf-8">
<title>KVTL Visitenkarte</title>
<link rel="stylesheet" href="https://fonts.googleapis.com/css2?family=Arimo:wght@400;700&display=swap">
<style>
  :root {
    --backdrop: #2b2b2b;
    --card-white: #f2f2f2;
    --card-white-edge: #dcdcdc;
    --panel-grey: #9d9d9d;
    --stripe-dark: #919191;
    --stripe-light: #e4e4e4;
    --logo-silver: #aaaaaa;
    --ink: #111111;
    --ink-soft: #2a2a2a;
    --ink-muted: #d6d6d6;
    --icon-circle: #c4c4c4;
  }
  * { box-sizing: border-box; margin: 0; padding: 0; }
  html, body {
    width: 1200px; height: 997px; overflow: hidden;
    background: var(--backdrop);
    font-family: "Arimo", Arial, sans-serif;
  }
  .business-card {
    position: absolute; left: 180px; top: 258px;
    width: 840px; height: 480px;
    border-radius: 26px; overflow: hidden;
    display: flex;
    box-shadow: 0 18px 40px rgba(0,0,0,.55);
  }
  .brand-side {
    width: 370px;
    background: linear-gradient(135deg, #ffffff, var(--card-white) 55%, var(--card-white-edge));
    display: flex; align-items: center; justify-content: center;
  }
  .brand-mark { display: flex; align-items: center; gap: 16px; }
  .brand-square { width: 44px; height: 44px; background: var(--logo-silver); }
  .brand-name {
    font-size: 68px; font-weight: 700; letter-spacing: 2px;
    color: var(--logo-silver);
  }
  .stripe-dark { width: 14px; background: var(--stripe-dark); }
  .stripe-light { width: 10px; background: var(--stripe-light); }
  .contact-side {
    flex: 1; background: var(--panel-grey);
    padding: 70px 40px 0 52px;
    color: var(--ink-soft);
  }
  .person-name { font-size: 28px; font-weight: 700; color: var(--ink); letter-spacing: .5px; }
  .person-role { font-size: 15px; color: var(--ink-muted); margin-top: 4px; letter-spacing: .5px; }
  .company-name { font-size: 14px; color: var(--ink-muted); margin-top: 46px; line-height: 1.25; letter-spacing: .4px; }
  .address { font-size: 21px; color: var(--ink); margin-top: 4px; line-height: 1.3; }
  .contact-list { list-style: none; margin-top: 30px; }
  .contact-item { display: flex; align-items: center; gap: 16px; font-size: 21px; color: var(--ink); margin-bottom: 14px; letter-spacing: .5px; }
  .contact-icon { width: 28px; height: 28px; flex: none; }
</style>
</head>
<body>
  <section class="business-card">
    <div class="brand-side">
      <div class="brand-mark">
        <span class="brand-square"></span>
        <span class="brand-name">KVTL</span>
      </div>
    </div>
    <div class="stripe-dark"></div>
    <div class="stripe-light"></div>
    <div class="contact-side">
      <h1 class="person-name">JONAS WEBER</h1>
      <p class="person-role">CO-FOUNDER</p>
      <p class="company-name">KELLTAL-HAUSSERVICE GMBH<br>&amp; CO. KG</p>
      <p class="address">Kellberger Str. 18 71489<br>Kellbach</p>
      <ul class="contact-list">
        <li class="contact-item">
          <svg class="contact-icon" viewBox="0 0 28 28" aria-hidden="true">
            <circle cx="14" cy="14" r="14" fill="var(--icon-circle)"/>
            <path d="M8 12c0-2 2-3 6-3s6 1 6 3v1h-3v-1.5h-6V13H8z M9 15h10l1 5H8z" fill="#8a8a8a"/>
          </svg>
          <span>07146-839214-0</span>
        </li>
        <li class="contact-item">
          <svg class="contact-icon" viewBox="0 0 28 28" aria-hidden="true">
            <circle cx="14" cy="14" r="14" fill="var(--icon-circle)"/>
            <rect x="7.5" y="9.5" width="13" height="9" fill="none" stroke="#8a8a8a" stroke-width="1.6"/>
            <path d="M7.5 9.5l6.5 5 6.5-5" fill="none" stroke="#8a8a8a" stroke-width="1.6"/>
          </svg>
          <span>Name@agentur-kvtl.de</span>
        </li>
      </ul>
    </div>
  </section>
</body>
</html>
```